Business Card for a Dental Office

The design should communicate integrity, quality and reliability. We also want the card look elegant, simple, but still stand out, different from the traditional-dental-office business card.

Industry/Entity Type

Business

```html
<!DOCTYPE html>
<html lang="en">
<head>
<meta charset="utf-8">
<title>Harbor Lane Dental – Business Card</title>
<link rel="stylesheet" href="https://fonts.googleapis.com/css2?family=Open+Sans:wght@400;600;700&display=swap">
<style>
  :root {
    --page: #e7e7e5;
    --card: #fbfbfa;
    --ink: #1b1b1b;
    --ink-soft: #2c2c2c;
    --gold: #b3901c;
    --gold-bright: #d8c21f;
    --rule: #222;
  }
  * { box-sizing: border-box; margin: 0; padding: 0; }
  html, body {
    width: 1200px; height: 970px; overflow: hidden;
    background: var(--page);
    font-family: "Open Sans", Arial, sans-serif;
    color: var(--ink);
  }
  .card {
    position: absolute; left: 100px; top: 207px;
    width: 1000px; height: 556px;
    background: var(--card);
    box-shadow: 0 6px 24px rgba(0,0,0,0.12);
    overflow: hidden;
  }
  .brand {
    position: absolute; left: 50px; top: 48px;
    display: flex; align-items: center; gap: 22px;
  }
  .brand__square {
    width: 112px; height: 112px; background: var(--ink);
  }
  .brand__name {
    font-family: "Open Sans", Arial, sans-serif;
    font-weight: 700; font-size: 40px; line-height: 1.1;
    text-transform: uppercase;
    color: var(--ink);
  }
  .brand__tagline {
    margin-top: 6px;
    font-family: "Open Sans", Arial, sans-serif;
    font-weight: 400; font-size: 20px;
    color: var(--gold);
  }
  .person {
    position: absolute; left: 48px; top: 286px; right: 48px;
  }
  .person__name { font-size: 26px; font-weight: 600; color: var(--ink); }
  .person__role-row { display: flex; align-items: center; gap: 12px; margin-top: 2px; }
  .person__role { font-size: 21px; color: var(--ink-soft); }
  .person__rule { flex: 1; height: 2px; background: var(--rule); margin-top: 6px; }
  .contacts {
    position: absolute; left: 48px; top: 384px;
    list-style: none; font-size: 21px; line-height: 32px; color: var(--ink-soft);
  }
  .contacts li { display: flex; align-items: center; gap: 8px; }
  .contacts svg { width: 22px; height: 18px; fill: var(--gold); flex: none; }
  .address {
    position: absolute; right: 48px; top: 416px;
    font-style: normal; text-align: right;
    font-size: 21px; line-height: 32px; color: var(--ink-soft);
  }
  .card__band {
    position: absolute; left: 0; right: 0; bottom: 0; height: 44px;
    background: linear-gradient(90deg, var(--gold) 0%, var(--gold-bright) 28%, #5a5316 44%, var(--ink) 52%, var(--ink) 100%);
    display: flex; align-items: center; justify-content: center;
  }
  .card__band-dot {
    width: 26px; height: 26px; border-radius: 50%; background: #fff; opacity: 0.85;
  }
</style>
</head>
<body>
  <article class="card">
    <header class="brand">
      <div class="brand__square"></div>
      <div>
        <div class="brand__name">Harbor Lane Dental</div>
        <div class="brand__tagline">Gentle care for every family</div>
      </div>
    </header>

    <section class="person">
      <h1 class="person__name">Marcus Hale, PHA</h1>
      <div class="person__role-row">
        <span class="person__role">President</span>
        <span class="person__rule"></span>
      </div>
    </section>

    <ul class="contacts">
      <li>
        <svg viewBox="0 0 22 18" aria-hidden="true"><path d="M2 6c0-3 4-4 9-4s9 1 9 4v2h-5V6H7v2H2z"/><path d="M5 9h12l2 7H3z"/></svg>
        + 000 000 0000
      </li>
      <li>
        <svg viewBox="0 0 22 18" aria-hidden="true"><rect x="6" y="1" width="10" height="5"/><rect x="2" y="6" width="18" height="8" rx="1"/><rect x="6" y="12" width="10" height="5" fill="#fff" stroke="#b3901c" stroke-width="1.5"/></svg>
        + 000 000 0000
      </li>
      <li>
        <svg viewBox="0 0 22 18" aria-hidden="true"><rect x="2" y="3" width="18" height="12"/><path d="M2 3l9 7 9-7" fill="none" stroke="#fbfbfa" stroke-width="1.6"/></svg>
        info@harborlanedental.com
      </li>
    </ul>

    <address class="address">
      Level 12, 48 Carrow Tower<br>
      Sydney, New South Wales
    </address>

    <footer class="card__band"><span class="card__band-dot"></span></footer>
  </article>
</body>
</html>
```